Business card design for Automotive workshop

We need a business card for a new automotive repair and tyre shop called Keelstone Prime Automotive located in New Zealand. We are a clean, modern and fresh workshop and company.

Front needs to feature logo,
my name:
Marlo Fenwicke (director)

Address:
48 Tarn Lane
Korimako Bay 3591

Phone: 07 594 2713
Mobile: 027 451 9362
Email: office@keelstoneautomotive.example.nz
Website: keelstoneautomotive.example.nz

Back needs to feature an area to write down appointment details, date and time.

Also feature a list of jobs and work we do such as,
Vehicle Servicing
All Mechanical Repairs
Warrant of Fitness
Tyres & Wheel Alignments
Automotive Diagnostics
Automotive Parts & Supplies

```html
<!DOCTYPE html>
<html lang="en">
<head>
<meta charset="utf-8">
<title>Keelstone Prime Automotive – Business Card</title>
<link href="https://fonts.googleapis.com/css2?family=Arimo:ital,wght@0,400;0,700;1,700&display=swap" rel="stylesheet">
<style>
  :root {
    --red: #e31e24;
    --ink: #1d1d1b;
    --grey: #b9b9b9;
    --paper: #ffffff;
    --backdrop: #333333;
  }
  * { box-sizing: border-box; margin: 0; padding: 0; }
  html, body { width: 1200px; height: 866px; overflow: hidden; background: var(--backdrop); }
  body { font-family: "Arimo", Arial, sans-serif; color: var(--ink); position: relative; }

  .card {
    position: absolute; left: 250px; width: 700px; height: 400px;
    background: var(--paper); overflow: hidden;
  }
  .card--front { top: 22px; }
  .card--back { top: 444px; }

  /* Front */
  .front-band { position: absolute; left: 0; right: 0; bottom: 0; height: 14px; background: var(--red); }
  .holder { position: absolute; left: 44px; top: 66px; }
  .holder__name { color: var(--red); font-weight: 700; font-size: 28px; letter-spacing: 0.5px; text-transform: uppercase; white-space: nowrap; }
  .holder__role { font-size: 20px; margin-top: 4px; }
  .divider { position: absolute; left: 300px; right: 40px; top: 196px; height: 1px; background: var(--grey); }
  .contacts { position: absolute; left: 44px; top: 150px; list-style: none; font-size: 19px; line-height: 27px; }
  .contacts li { display: flex; align-items: center; gap: 8px; white-space: nowrap; }
  .contacts svg { width: 16px; height: 16px; flex: none; }
  .brand { position: absolute; right: 44px; top: 64px; display: flex; align-items: center; gap: 12px; }
  .brand__mark { width: 16px; height: 16px; background: var(--ink); }
  .brand__name { color: var(--red); font-weight: 700; font-size: 24px; line-height: 28px; text-transform: uppercase; letter-spacing: 1px; text-align: right; white-space: nowrap; }
  .address { position: absolute; right: 44px; bottom: 44px; text-align: right; font-size: 21px; line-height: 26px; white-space: nowrap; }

  /* Back */
  .appointment { position: absolute; left: 0; right: 0; top: 0; height: 186px; }
  .appointment__title { position: absolute; right: 60px; top: 34px; color: var(--red); font-weight: 700; font-style: italic; font-size: 25px; text-transform: uppercase; }
  .field { position: absolute; left: 70px; display: flex; align-items: flex-end; gap: 14px; font-size: 19px; text-transform: uppercase; }
  .field--date { top: 80px; }
  .field--time { top: 128px; left: 100px; }
  .field__line { width: 470px; height: 1px; background: var(--grey); margin-bottom: 4px; }
  .field--time .field__line { width: 440px; }
  .services-band { position: absolute; left: 0; right: 0; top: 186px; bottom: 0; background: var(--red); border-top: 4px solid var(--ink); }
  .services { position: absolute; list-style: none; color: var(--paper); font-size: 19px; line-height: 28px; white-space: nowrap; }
  .services li::before { content: "\25CF"; font-size: 12px; margin-right: 8px; vertical-align: 3px; }
  .services--first { left: 60px; top: 28px; }
  .services--second { left: 340px; top: 110px; }
</style>
</head>
<body>

<section class="card card--front" aria-label="Business card front">
  <div class="holder">
    <div class="holder__name">Marlo Fenwicke</div>
    <div class="holder__role">Director</div>
  </div>
  <ul class="contacts">
    <li><svg viewBox="0 0 16 16" aria-hidden="true"><path fill="#e31e24" d="M3 2h3l1 3-2 1.5a8 8 0 0 0 4.5 4.5L11 9l3 1v3a1 1 0 0 1-1 1A12 12 0 0 1 2 3a1 1 0 0 1 1-1z"/></svg>07 594 2713</li>
    <li><svg viewBox="0 0 16 16" aria-hidden="true"><rect x="4" y="1" width="8" height="14" rx="1.5" fill="none" stroke="#e31e24" stroke-width="1.8"/></svg>027 451 9362</li>
    <li><svg viewBox="0 0 16 16" aria-hidden="true"><rect x="1" y="3" width="14" height="10" fill="#e31e24"/><path d="M1 3l7 6 7-6" fill="none" stroke="#fff" stroke-width="1.4"/></svg>office@keelstoneautomotive.example.nz</li>
    <li><svg viewBox="0 0 16 16" aria-hidden="true"><circle cx="8" cy="8" r="7" fill="#e31e24"/><path d="M1 8h14M8 1c-3 4-3 10 0 14M8 1c3 4 3 10 0 14" fill="none" stroke="#fff" stroke-width="1"/></svg>keelstoneautomotive.example.nz</li>
  </ul>
  <div class="divider"></div>
  <div class="brand">
    <div class="brand__mark"></div>
    <div class="brand__name">Keelstone Prime<br>Automotive</div>
  </div>
  <div class="address">48 Tarn Lane<br>Korimako Bay 3591</div>
  <div class="front-band"></div>
</section>

<section class="card card--back" aria-label="Business card back">
  <div class="appointment">
    <div class="appointment__title">Next Appointment</div>
    <div class="field field--date"><span>Date</span><span class="field__line"></span></div>
    <div class="field field--time"><span>Time</span><span class="field__line"></span></div>
  </div>
  <div class="services-band">
    <ul class="services services--first">
      <li>Vehicle Servicing</li>
      <li>All Mechanical Repairs</li>
      <li>Warrant of Fitness</li>
    </ul>
    <ul class="services services--second">
      <li>Tyres &amp; Wheel Alignments</li>
      <li>Automotive Diagnostics</li>
      <li>Automotive Parts &amp; Supplies</li>
    </ul>
  </div>
</section>

</body>
</html>
```